PixelHarbor Rangers (Ledgerline Nova)
A website dedicated to crypto education. We are a new company focused on blockchain edutainment (education and interesting and entertaining content about the blockchain space). We want a fun, clean/minimalist and modern website that is made up of an education platform which could be a website in it’s own right. It will be the reference point for our users/community for all of our other blockchain based content in the PHR website ecosystem which will be covering; crypto news, digital asset investing (including a technical and fundamental analysis subscription service), blockchain business solutions and an NFT section that will cover creative art projects (art, music, gaming and more). To feature a logins and payment system which may need a shopping basket set up for tutorial/educational platform that is accessed via the website, NFT page with sub-categories: education and NFT and metaverse/virtual world and merchandise shopping page which is Web 3.0 enabled (able to link to a VeloPurse, Tandem Vault etc , digital asset education page featuring blog and newsletter subscriptions links, A social media page where people can access videos, podcasts and our presence on other platforms such as Chirplo, Snapmora, Huddlex, Wirepost etc.
Number of Pages Required
5+ page
Look and feel

```html
<!DOCTYPE html>
<html lang="en">
<head>
<meta charset="utf-8">
<title>PixelHarbor Rangers</title>
<link href="https://fonts.googleapis.com/css2?family=Bree+Serif&family=Roboto+Slab:wght@400;500;700&family=Roboto:wght@400;500&display=swap" rel="stylesheet">
<style>
:root{
  --night:#0b0d24;
  --card:#141838;
  --violet:#5a0ae6;
  --violet-btn:#6a0dff;
  --orchid:#8c14e8;
  --accent-line:#5b12ea;
  --white:#ffffff;
  --lavender:#d9c8ff;
  --muted:#c9cbe0;
  --magenta:#d21ee6;
  --lime:#5cf03a;
  --cyan:#2fb4ff;
  --footer:#0c0d22;
}
*{margin:0;padding:0;box-sizing:border-box}
html,body{width:1200px;height:3650px;overflow:hidden}
body{background:var(--night);color:var(--white);font-family:"Roboto Slab",serif;position:relative}
section,header,footer{position:absolute;left:0;width:1200px}
.abs{position:absolute}
.center{text-align:center;left:0;width:1200px}
.section-title{position:absolute;left:0;width:1200px;text-align:center;font-weight:700;font-size:38px}
.rule{position:absolute;left:577px;width:46px;height:3px;background:var(--accent-line)}
.rule.light{background:var(--white)}
.sprite{position:absolute;border-radius:8px}

.hero{top:0;height:762px;background:radial-gradient(ellipse at 50% 85%,#3a1d55 0%,#1a1740 40%,#0b0d2c 75%,#080a1e 100%)}
.hero-art{position:absolute;inset:0;background:linear-gradient(180deg,rgba(40,40,110,.35) 0%,rgba(10,12,40,0) 40%,rgba(120,30,80,.25) 100%)}
.brand{left:110px;top:26px;width:190px;text-align:center;font-family:"Bree Serif",serif;font-size:34px;line-height:40px}
.btn-pill{position:absolute;top:22px;height:41px;border-radius:21px;background:var(--violet-btn);font-size:13px;font-weight:700;line-height:41px;text-align:center}
.nav{position:absolute;top:90px;font-size:13px;font-weight:500;letter-spacing:.3px}
.hero h1{top:340px;font-size:52px;font-weight:700;letter-spacing:1px}
.hero p.lead{top:420px;font-size:20px;line-height:35px;color:#e8e8f4}
.get-started{left:513px;top:513px;width:174px;height:57px;border-radius:29px;background:var(--violet-btn);font-weight:700;font-size:19px;line-height:57px;text-align:center}

.ecosystem{top:762px;height:686px;background:var(--night)}
.eco-card{position:absolute;width:471px;height:205px;background:var(--card);border-radius:6px}
.eco-media{position:absolute;left:10px;top:15px;width:186px;height:176px;border-radius:4px}
.eco-card h3{position:absolute;left:230px;top:36px;width:225px;font-size:19px;line-height:27px;font-weight:700}
.eco-card .mini{position:absolute;left:230px;top:76px;width:36px;height:2px;background:var(--accent-line)}
.eco-card p{position:absolute;left:230px;top:95px;width:225px;font-family:"Roboto",sans-serif;font-size:13px;line-height:26px;color:var(--muted)}
.eco-card.two-line h3{top:18px}

.creative{top:1448px;height:475px;background:var(--violet)}
.feature{position:absolute;top:157px;width:300px;text-align:center}
.feature .ring{width:145px;height:145px;margin:0 auto;border:2px solid var(--white);border-radius:50%;display:flex;align-items:center;justify-content:center}
.feature h3{margin-top:10px;font-size:24px;font-weight:700}
.feature p{margin-top:12px;font-size:14px;line-height:25px;color:#ece6ff}

.tutorial{top:1923px;height:564px;background:var(--night)}
.video{position:absolute;top:143px;width:467px;height:284px}
.play{position:absolute;left:50%;top:50%;width:84px;height:84px;margin:-42px 0 0 -42px}
.video-caption{position:absolute;top:452px;font-size:18px}
.price{position:absolute;top:454px;font-size:17px}
.socials{position:absolute;top:495px;font-family:"Roboto",sans-serif;font-size:13px;color:var(--muted);letter-spacing:.2px}

.asset-ed{top:2487px;height:387px;background:var(--violet)}
.asset-ed p{top:125px;font-size:17px;line-height:35px;color:var(--lavender)}
.outline-btn{position:absolute;top:268px;width:151px;height:57px;border:2px solid var(--white);border-radius:29px;text-align:center;line-height:53px;font-size:18px}

.nft-ed{top:2874px;height:456px;background:var(--orchid)}
.nft-ed .sub{top:120px;font-size:18px;color:var(--lavender)}
.nft-tile{position:absolute;top:176px;width:311px;height:208px}
.chev{position:absolute;top:233px;width:20px;height:70px}

.site-footer{top:3330px;height:320px;background:var(--footer)}
.wallet{position:absolute;font-family:"Roboto",sans-serif;font-weight:500;display:flex;align-items:center;gap:12px}
.wallet .mark{width:30px;height:30px;border-radius:50%;background:#f08a2c}
.wallet .mark.sq{border-radius:8px;background:var(--white)}
.divider{position:absolute;top:68px;width:1px;height:125px;background:#2b2e4c}
.info-title{position:absolute;font-family:"Roboto",sans-serif;font-size:20px;font-weight:500}
.info-text{position:absolute;font-family:"Roboto",sans-serif;font-size:13px;line-height:23px;color:#d7d8e6}
.social-ring{position:absolute;top:158px;width:40px;height:40px;border:2px solid var(--white);border-radius:50%}
.copyright{top:272px;font-family:"Roboto",sans-serif;font-size:16px}
.pay{position:absolute;top:265px;width:30px;height:20px;border-radius:3px}
</style>
</head>
<body>

<header class="hero">
  <div class="hero-art" role="img" aria-label="Dark digital network backdrop with glowing pink and blue data points"></div>
  <div class="abs brand">PixelHarbor<br>Rangers</div>
  <div class="btn-pill" style="left:785px;width:121px">REGISTER</div>
  <div class="btn-pill" style="left:915px;width:174px">USER COMMUNITY</div>
  <nav>
    <span class="nav" style="left:482px">HOME</span>
    <span class="nav" style="left:580px">ABOUT US</span>
    <span class="nav" style="left:705px">NFT</span>
    <span class="nav" style="left:788px">BLOG</span>
    <span class="nav" style="left:882px">GALLERY</span>
    <span class="nav" style="left:1001px">CONTACT US</span>
  </nav>
  <h1 class="abs center">PIXELHARBOR RANGERS</h1>
  <p class="abs center lead">Sed ut perspiciatis unde omnis iste natus error sit voluptatem sit<br>accusantium doloremque laudantium</p>
  <div class="abs get-started">Get Started</div>
</header>

<section class="ecosystem">
  <h2 class="section-title" style="top:48px">PHR Ecosystem</h2>
  <div class="rule" style="top:110px"></div>
  <div class="sprite" style="left:968px;top:30px;width:107px;height:98px;background:#5d1ee8" role="img" aria-label="Pixel space invader character"></div>

  <div class="eco-card" style="left:110px;top:156px">
    <div class="eco-media" style="background:linear-gradient(135deg,#4a3a2c,#1b1a24)" role="img" aria-label="Hand holding phone with coin graphics"></div>
    <h3>Crypto News</h3><div class="mini"></div>
    <p>Sed ut perspiciatis unde omnis iste natus error sit voluptatem accusant ium doloremque laudantium</p>
  </div>
  <div class="eco-card" style="left:618px;top:156px">
    <div class="eco-media" style="background:linear-gradient(135deg,#1e3a5a,#0e1626)" role="img" aria-label="Typing on laptop with network blocks"></div>
    <h3>Digital Asset Investing</h3><div class="mini"></div>
    <p>Sed ut perspiciatis unde omnis iste natus error sit voluptatem accusant ium doloremque laudantium</p>
  </div>
  <div class="eco-card two-line" style="left:110px;top:400px">
    <div class="eco-media" style="background:linear-gradient(135deg,#0f2a3a,#3a2414)" role="img" aria-label="Glowing connected blocks"></div>
    <h3>Blockchain Business Solutions</h3><div class="mini"></div>
    <p>Sed ut perspiciatis unde omnis iste natus error sit voluptatem accusant ium doloremque laudantium</p>
  </div>
  <div class="eco-card" style="left:618px;top:400px">
    <div class="eco-media" style="background:linear-gradient(135deg,#1a3ad8,#0a1030)" role="img" aria-label="Blue glowing cubes"></div>
    <h3>NFT</h3><div class="mini"></div>
    <p>Sed ut perspiciatis unde omnis iste natus error sit voluptatem accusant ium doloremque laudantium</p>
  </div>
</section>

<section class="creative">
  <h2 class="section-title" style="top:42px">Creative Art Projects</h2>
  <div class="rule light" style="top:102px"></div>
  <div class="sprite" style="left:127px;top:37px;width:108px;height:67px;background:var(--lime)" role="img" aria-label="Pixel cat character"></div>

  <div class="feature" style="left:116px">
    <div class="ring"><svg width="64" height="64" viewBox="0 0 64 64" fill="none" stroke="#fff" stroke-width="2.5" stroke-linecap="round"><path d="M14 50 L44 20 L50 26 L20 56 L12 58 Z"/><path d="M40 24 L46 30"/><path d="M14 14 L50 50"/></svg></div>
    <h3>Art</h3>
    <p>Sed ut perspiciatis unde omnis iste<br>natus error sit voluptatem</p>
  </div>
  <div class="feature" style="left:454px">
    <div class="ring"><svg width="64" height="64" viewBox="0 0 64 64" fill="none" stroke="#fff" stroke-width="2.5"><path d="M24 46 V16 L50 10 V40"/><path d="M24 22 L50 16"/><circle cx="18" cy="46" r="6"/><circle cx="44" cy="40" r="6"/></svg></div>
    <h3>Music</h3>
    <p>Sed ut perspiciatis unde omnis iste<br>natus error sit voluptatem</p>
  </div>
  <div class="feature" style="left:790px">
    <div class="ring"><svg width="68" height="64" viewBox="0 0 68 64" fill="none" stroke="#fff" stroke-width="2.5" stroke-linecap="round"><rect x="8" y="24" width="52" height="28" rx="10"/><path d="M34 24 V12"/><circle cx="22" cy="38" r="4"/><path d="M44 38 h8 M48 34 v8"/></svg></div>
    <h3>Gaming</h3>
    <p>Sed ut perspiciatis unde omnis iste<br>natus error sit voluptatem</p>
  </div>
</section>

<section class="tutorial">
  <h2 class="section-title" style="top:42px">PixelHarbor Tutorial</h2>
  <div class="rule" style="top:100px"></div>
  <div class="sprite" style="left:968px;top:17px;width:134px;height:115px;background:var(--magenta)" role="img" aria-label="Pixel robot character"></div>

  <div class="video" style="left:110px;background:linear-gradient(135deg,#123a6a,#0a1a36 60%,#1d2a44)" role="img" aria-label="Developer working on a laptop in a server room">
    <svg class="play" viewBox="0 0 84 84"><circle cx="42" cy="42" r="40" fill="rgba(0,0,0,.25)" stroke="#fff" stroke-width="2"/><path d="M34 28 L58 42 L34 56 Z" fill="#fff"/></svg>
  </div>
  <div class="video-caption" style="left:110px">Sed ut perspiciatis unde omnis</div>
  <div class="price" style="left:535px">Free</div>
  <div class="socials" style="left:110px">Chirplo · Snapmora · Huddlex · Wirepost</div>

  <div class="video" style="left:623px;background:linear-gradient(135deg,#0e2a40,#134a6a 50%,#3a3a1a)" role="img" aria-label="Glowing padlock on a circuit board">
    <svg class="play" viewBox="0 0 84 84"><circle cx="42" cy="42" r="40" fill="rgba(0,0,0,.25)" stroke="#fff" stroke-width="2"/><path d="M34 28 L58 42 L34 56 Z" fill="#fff"/></svg>
  </div>
  <div class="video-caption" style="left:623px">Sed ut perspiciatis unde omnis</div>
  <div class="price" style="left:1047px">Paid</div>
  <div class="socials" style="left:623px">Chirplo · Snapmora · Huddlex · Wirepost</div>
</section>

<section class="asset-ed">
  <h2 class="section-title" style="top:48px">Digital Asset Education</h2>
  <div class="rule light" style="top:106px"></div>
  <div class="sprite" style="left:58px;top:53px;width:82px;height:85px;background:var(--cyan)" role="img" aria-label="Pixel alien character"></div>
  <div class="sprite" style="left:1040px;top:223px;width:135px;height:116px;background:var(--magenta)" role="img" aria-label="Pixel robot character"></div>
  <p class="abs center">Sed ut perspiciatis unde omnis iste natus error sit voluptatem accusantium doloremque<br>laudantium, totam rem aperiam, eaque ipsa quae ab illo inventore veritatis et quasi archit<br>ecto beatae vitae dicta sunt explicabo.</p>
  <div class="outline-btn" style="left:443px">SIGNUP</div>
  <div class="outline-btn" style="left:606px">BLOG</div>
</section>

<section class="nft-ed">
  <h2 class="section-title" style="top:45px">NFT Education</h2>
  <div class="rule light" style="top:100px"></div>
  <p class="abs center sub">Sed ut perspiciatis unde omnis iste natus error sit voluptatem accusantium</p>
  <svg class="chev" style="left:54px" viewBox="0 0 20 70" fill="none" stroke="#fff" stroke-width="1.5"><path d="M16 2 L4 35 L16 68"/></svg>
  <svg class="chev" style="left:1134px" viewBox="0 0 20 70" fill="none" stroke="#fff" stroke-width="1.5"><path d="M4 2 L16 35 L4 68"/></svg>
  <div class="nft-tile" style="left:110px;background:linear-gradient(135deg,#2a2a9a,#101050)" role="img" aria-label="Blue circuit board pattern">
    <svg class="play" viewBox="0 0 84 84"><circle cx="42" cy="42" r="36" fill="rgba(0,0,0,.2)" stroke="#fff" stroke-width="2"/><path d="M35 30 L56 42 L35 54 Z" fill="#fff"/></svg>
  </div>
  <div class="nft-tile" style="left:446px;background:linear-gradient(135deg,#2a2224,#6a3a30 50%,#1a1a20)" role="img" aria-label="Hand holding glowing NFT lettering">
    <svg class="play" viewBox="0 0 84 84"><circle cx="42" cy="42" r="36" fill="rgba(0,0,0,.2)" stroke="#fff" stroke-width="2"/><path d="M35 30 L56 42 L35 54 Z" fill="#fff"/></svg>
  </div>
  <div class="nft-tile" style="left:779px;background:linear-gradient(135deg,#14181a,#2a3a22 55%,#0c1a2a)" role="img" aria-label="Hands with glowing NFT tablet">
    <svg class="play" viewBox="0 0 84 84"><circle cx="42" cy="42" r="36" fill="rgba(0,0,0,.2)" stroke="#fff" stroke-width="2"/><path d="M35 30 L56 42 L35 54 Z" fill="#fff"/></svg>
  </div>
</section>

<footer class="site-footer">
  <div class="wallet" style="left:148px;top:82px;font-size:22px;letter-spacing:4px"><span class="mark"></span>VELOPURSE</div>
  <div class="wallet" style="left:145px;top:140px;font-size:26px"><span class="mark sq" style="width:50px;height:50px"></span>Tandem Vault</div>

  <div class="divider" style="left:443px"></div>
  <svg class="abs" style="left:465px;top:80px" width="18" height="24" viewBox="0 0 18 24" fill="none" stroke="#d7d8e6" stroke-width="1.6"><path d="M9 23 C4 16 2 12 2 9 A7 7 0 0 1 16 9 C16 12 14 16 9 23 Z"/><circle cx="9" cy="9" r="2.5"/></svg>
  <div class="info-title" style="left:503px;top:66px">ADDRESS</div>
  <div class="info-text" style="left:503px;top:94px"># 254 Harbor Lane<br>Bayside District</div>
  <div class="social-ring" style="left:503px" role="img" aria-label="Professional network link"></div>
  <div class="social-ring" style="left:556px" role="img" aria-label="Social network link"></div>

  <div class="divider" style="left:772px"></div>
  <svg class="abs" style="left:808px;top:82px" width="20" height="20" viewBox="0 0 20 20" fill="none" stroke="#d7d8e6" stroke-width="1.5"><path d="M4 2 L8 2 L9 6 L7 8 C8 11 10 13 12 14 L14 12 L18 13 L18 17 C10 18 2 10 4 2 Z"/></svg>
  <div class="info-title" style="left:847px;top:66px">PHONE</div>
  <div class="info-text" style="left:847px;top:94px">+1 555 014 2290</div>
  <svg class="abs" style="left:808px;top:147px" width="22" height="16" viewBox="0 0 22 16" fill="none" stroke="#d7d8e6" stroke-width="1.5"><rect x="1" y="1" width="20" height="14"/><path d="M1 1 L11 9 L21 1"/></svg>
  <div class="info-title" style="left:850px;top:136px">EMAIL</div>
  <div class="info-text" style="left:850px;top:164px">hello@pixelharbor.example</div>

  <div class="abs center copyright">© 2022 PixelHarbor Rangers.All rights reserved.</div>
  <div class="pay" style="left:920px;background:#f2f2f2"></div>
  <div class="pay" style="left:954px;background:#e8e8e8"></div>
  <div class="pay" style="left:988px;background:#dfe6f0"></div>
  <div class="pay" style="left:1022px;background:#eeeeee"></div>
  <div class="pay" style="left:1056px;background:#e6ecf4"></div>
</footer>

</body>
</html>
```